Web design for facial expression recognition service

We offer a service which allows customers to film large panels of participants looking at some video/screen (e.g. an advertisement) and to analyze the facial expressions shown by the participants. We are looking for the design of a new website which will make it easy for our customers to setup and view the results of these experiments online.
Competitor's websites that may serve as a reference are:
http://www.moriventa.com/quelbo/#pane_overview
http://www.dunvarpix.com/homepage.aspx
https://www.tamlora.com/
The website will (for as far as the design is concerned) consist of three parts:
- A public home page (and perhaps some contact/news/about page), designed to catch the attention/interest potential customers.
- A (protected) project result page, showing the results in an interactive page with charts and numerical data.
- Pages (also protected) with fields and tables (setting up the project details).
The winner of this design project should provide us with at least one design for each of the above in order to get a complete 'theme' going which our developers can use. However, you are welcome to initially only provide the design for the project result page and/or home page.
We are looking for a modern, fresh, yet professional look (my client is a more established party in the field).
The final delivery should consist of layered Photoshop or Illustrator files.
Thank you in advance for participating!
Updates
Dear designers,
Project Deadline Extended
Reason: Extending the deadline by a few days to give designers a chance to submit designs for the other pages and process further feedback.
Target Market(s)
marketing research agencies (B2B service)
Requirements
Must have
- Home page:
- Basic advertisement of the service; some quick explanation of how it works
- A way to login for existing users
- A link/button/banner inviting people to sign up
- Navigation controls to 2-3 other pages
- Social media links (Facebook, LinkedIn group)
- Company logo (sorry, can't provide it as my client wishes to remain anonymous for now, but it's rounded and has blue as it's main color).
- Copyright / creator details
Project result page:
(see attachment 1 for a functional mockup - the design may follow this layout closely, or be completely different)
- Title
- A video player and basic numerical data
- Different views of the analysis results can dynamically be added/removed/collapsed/expanded; each one of these views will show some kind of chart, filters (combos), numerical data and a download button/link.
- A way to sign out, go to the main project page and go to the main page
- Logo
- Copyright
The form pages:
(see attachment 2 for a functional mockup of one of the pages; feel free to change some elements to better show the overall style)
- Title
- Text fields, combos, calendar pickers, tables, navigation links
- Logo
- Copyright
Nice to have
- Any creative text elements or product logo/symbol are a bonus. However, the basic "Lorem Ipsum" would do too.

```html
<!DOCTYPE html>
<html lang="en">
<head>
<meta charset="utf-8">
<title>Velmora — Facial Expression Analysis</title>
<link href="https://fonts.googleapis.com/css2?family=Ubuntu:wght@400;500;700&family=Arimo:wght@400;700&display=swap" rel="stylesheet">
<style>
:root{
  --blue:#2a8ccc;
  --blue-dark:#1b6fae;
  --sky:#d7ebf7;
  --sky-pale:#eef6fc;
  --green:#3a9d23;
  --green-dark:#2c7d12;
  --text:#555;
  --text-dark:#111;
  --rule:#e3e3e3;
  --footer:#3a3a3a;
  --footer-text:#e6e6e6;
}
*{margin:0;padding:0;box-sizing:border-box}
html,body{width:766px;height:1200px;overflow:hidden;background:#fff}
body{position:relative;font-family:Arimo,Arial,sans-serif;color:var(--text)}
.abs{position:absolute}
.heading{font-family:Ubuntu,sans-serif;font-weight:400;color:var(--blue)}

/* header */
.top-band{left:0;top:46px;width:766px;height:12px;background:var(--sky)}
.hero-bg{left:0;top:58px;width:766px;height:272px;background:linear-gradient(#e6f2fb,#f4f9fd);border-bottom:2px solid #dbe6ee}
.nav{left:430px;top:11px;display:flex;align-items:center;font-family:Ubuntu,sans-serif;font-size:10.5px;color:#333}
.nav a{color:#333;text-decoration:none;padding:0 10px;border-left:1px solid #bbb;line-height:13px}
.nav a.active{background:var(--blue);color:#fff;border:none;border-radius:2px;padding:4px 8px;margin-right:8px}
.nav a.active + a{border-left:none;border-left:1px solid #bbb}
.logo{left:56px;top:24px;width:184px;height:52px;background:#fff;border-radius:26px;box-shadow:0 2px 5px rgba(0,0,0,.12);display:flex;align-items:center;justify-content:center;font-family:Ubuntu,sans-serif;font-weight:500;font-size:26px;color:var(--blue)}
.video-label{left:142px;top:112px;width:134px;height:28px;background:rgba(40,40,40,.08);border-radius:3px}
.video{left:58px;top:144px;width:336px;height:232px;background:#fff;box-shadow:0 2px 5px rgba(0,0,0,.2)}
.video-screen{left:4px;top:4px;width:328px;height:221px;background:linear-gradient(135deg,#0d1a26,#1d3a52 55%,#06090c)}
.play{left:144px;top:94px;width:45px;height:32px;background:rgba(0,0,0,.75);border-radius:6px;border:1px solid #555}
.reflection{left:62px;top:378px;width:328px;height:24px;background:linear-gradient(rgba(200,200,200,.35),rgba(255,255,255,0))}
.hero-art{left:396px;top:60px;width:312px;height:270px;background:radial-gradient(ellipse at 50% 40%,#b9d6f0,#7fa9d6 60%,#dbeaf7)}
.slider-arrows{left:686px;top:310px;display:flex;gap:1px}
.slider-arrows span{width:11px;height:14px;background:#555;border-radius:7px 0 0 7px}
.slider-arrows span + span{border-radius:0 7px 7px 0}
.hero-note{left:414px;top:348px;width:176px;font-size:9.2px;line-height:13.5px;color:#555}
.signup{left:592px;top:346px;width:117px;height:30px;border-radius:15px;background:linear-gradient(#5cc434,#2f8a12);box-shadow:0 2px 4px rgba(0,0,0,.25);color:#fff;font-family:Arimo,sans-serif;font-weight:700;font-size:13px;display:flex;align-items:center;justify-content:center}

.rule{left:58px;width:652px;height:1px;background:var(--rule)}

/* how it works */
.how-title{left:58px;top:425px;font-size:16px}
.how-text{left:58px;top:451px;width:652px;font-size:9px;line-height:14.5px}

.steps-band{left:0;top:520px;width:766px;height:200px;background:linear-gradient(#f5f5f5,#fcfcfc)}
.step{top:531px;width:198px;height:180px;background:#fff;border-radius:4px}
.step h3{font-family:Ubuntu,sans-serif;font-weight:400;font-size:14px;color:var(--green);margin:10px 0 0 16px}
.step p{font-size:8.4px;line-height:14.5px;margin:6px 14px 0 16px;text-align:justify}
.step .icon{position:absolute;left:50%;transform:translateX(-50%);background:linear-gradient(#e4edf5,#bcccd9);border-radius:6px}

/* about + login */
.about-title{left:59px;top:757px;font-size:16px}
.about-lead{left:59px;top:785px;width:426px;font-size:9.2px;line-height:14.5px;color:var(--text-dark)}
.about-text{left:59px;top:819px;width:426px;font-size:9px;line-height:14.6px;text-align:justify}
.login{left:506px;top:760px;width:198px;height:144px;background:linear-gradient(#4a9fd8,#1f6fb0);border-radius:3px;box-shadow:0 3px 6px rgba(0,0,0,.2)}
.login h3{position:absolute;left:42px;top:14px;font-family:Ubuntu,sans-serif;font-weight:400;font-size:16px;color:#fff}
.login .field{position:absolute;left:11px;width:176px;height:18px;background:#f4f4f4;border:1px solid #d0d6dc;font-size:7px;color:#666;padding:5px 9px}
.login .submit{position:absolute;left:126px;top:110px;width:60px;height:21px;background:linear-gradient(#333,#000);border-radius:3px;color:#fff;font-size:9.5px;font-weight:700;display:flex;align-items:center;justify-content:center;letter-spacing:.3px}

/* testimonials */
.testi-title{left:57px;top:950px;font-size:16px}
.testi-arrows{left:690px;top:954px}
.quote{top:984px;width:182px;font-size:10px;line-height:14.6px;text-align:justify}
.quote p + p{margin-top:4px}
.quote .name{margin-top:10px;color:var(--blue);font-size:11px}
.quote .city{margin-top:3px;color:var(--text-dark);font-size:9px}
.vsep{top:980px;width:1px;height:140px;background:var(--rule)}

/* footer */
.footer{left:0;top:1140px;width:766px;height:60px;background:var(--footer);color:var(--footer-text);font-size:8.2px}
.footer .links{position:absolute;left:58px;top:16px}
.footer .copy{position:absolute;left:58px;top:34px}
.social{position:absolute;top:17px;width:24px;height:24px;border-radius:50%;background:linear-gradient(#39a9ea,#0b6fb8);border:2px solid #fff}
</style>
</head>
<body>

<header>
  <div class="abs top-band"></div>
  <div class="abs hero-bg"></div>
  <nav class="abs nav">
    <a class="active" href="#">Home</a>
    <a href="#" style="border-left:none">About</a>
    <a href="#">Products</a>
    <a href="#">Blog</a>
    <a href="#">Contact</a>
  </nav>
  <div class="abs logo">Velmora</div>
</header>

<section class="hero">
  <div class="abs video-label" role="img" aria-label="Hand-lettered 'Demo Video' label with arrow"></div>
  <div class="abs video">
    <div class="abs video-screen" role="img" aria-label="Demo video still of face recognition software">
      <div class="abs play">
        <svg width="45" height="32" viewBox="0 0 45 32"><path d="M18 9 L29 16 L18 23 Z" fill="#fff"/></svg>
      </div>
    </div>
  </div>
  <div class="abs reflection"></div>
  <div class="abs hero-art" role="img" aria-label="Illustration of a wireframe mesh over a human head"></div>
  <div class="abs slider-arrows"><span></span><span></span></div>
  <p class="abs hero-note">Praesent malesuada, nisl et fermentum sollicitudin, dui sem porta massa</p>
  <a class="abs signup">Signup Now</a>
</section>

<div class="abs rule" style="top:410px"></div>

<section class="how">
  <h2 class="abs heading how-title">How it works</h2>
  <p class="abs how-text">Praesent malesuada, nisl et fermentum sollicitudin, dui sem porta massa, non imperdiet diam elit et mi. Sed in velit at turpis varius gravida bibendum at neque. Cras ac quam erat, quis convallis nisi. Mauris enim nisl, convallis sed sodales vitae, feugiat eget ligula. Vivamus felis purus, iaculis at mattis ultricies, venenatis eget lorem. Vivamus vestibulum euismod facilisis. Vestibulum imperdiet tellus purus.</p>
  <div class="abs steps-band"></div>
  <article class="abs step" style="left:64px">
    <h3>Step 1&nbsp; - &nbsp;Title Goes Here</h3>
    <p>Praesent dictum latrn vestibulum tristique. Maecenas consectetur accumsan lacus ac dignissim, nunc nunc laoreet nunc.</p>
    <div class="icon" role="img" aria-label="Illustration of a hard drive with a download arrow" style="top:88px;width:68px;height:52px"></div>
  </article>
  <article class="abs step" style="left:284px">
    <h3>Step 2&nbsp; - &nbsp;Title Goes Here</h3>
    <p>Praesent dictum latrn vestibulum tristique. Maecenas consectetur accumsan lacus ac dignissim, nunc nunc laoreet nunc.</p>
    <div class="icon" role="img" aria-label="Illustration of a laptop with a webcam" style="top:90px;width:140px;height:82px"></div>
  </article>
  <article class="abs step" style="left:504px">
    <h3>Step 3&nbsp; - &nbsp;Title Goes Here</h3>
    <p>Praesent dictum latrn vestibulum tristique. Maecenas consectetur accumsan lacus ac dignissim, nunc nunc laoreet nunc.</p>
    <div class="icon" role="img" aria-label="Illustration of a mask with tracking points" style="top:92px;width:50px;height:62px;border-radius:20px"></div>
  </article>
</section>

<div class="abs rule" style="top:737px"></div>

<section class="about">
  <h2 class="abs heading about-title">About Velmora</h2>
  <p class="abs about-lead">Nulla imperdiet lorem eget neque dictum porta. Vestibulum ante ipsum primis in faucibus orci luctus et ultrices posuere cubilia Curae;</p>
  <p class="abs about-text">Nam aliquam porta mauris, vitae pharetra massa fermentum a. Maecenas lobortis nisl et massa venenatis eu fringilla dolor vehicula. Cras lacinia mollis diam, non feugiat sem venenatis nec. Cras non elit et nulla consequat cursus nec vel magna. Donec ipsum lacus, feugiat sit amet eleifend eget, lacinia vel libero. Nunc ultrices nulla adipiscing magna accumsan congue. Suspendisse est justo, porta ut lacinia at, bibendum non neque. Vestibulum pellentesque velit vel erat elementum in tempor velit luctus. Sed iaculis venenatis quam a commodo. Phasellus ac odio vitae ligula ultricies</p>
  <form class="abs login">
    <svg class="abs" style="left:14px;top:10px" width="22" height="28" viewBox="0 0 22 28">
      <path d="M5 12 V8 a6 6 0 0 1 12 0 V12" fill="none" stroke="#dfe6ec" stroke-width="3"/>
      <rect x="2" y="12" width="18" height="15" rx="2" fill="#cfd8df" stroke="#8a96a0"/>
    </svg>
    <h3>Member Login</h3>
    <div class="field" style="top:54px">Username</div>
    <div class="field" style="top:82px">Password</div>
    <div class="submit">SUBMIT</div>
  </form>
</section>

<div class="abs rule" style="top:933px"></div>

<section class="testimonials">
  <h2 class="abs heading testi-title">Testimonials</h2>
  <svg class="abs testi-arrows" width="16" height="10" viewBox="0 0 16 10"><path d="M5 1 L1 5 L5 9 M11 1 L15 5 L11 9" fill="none" stroke="#555" stroke-width="1.6"/></svg>
  <blockquote class="abs quote" style="left:63px">
    <p>“ Neque porro quisquam est, qui dolorem ipsum quia dolor sit amet.</p>
    <p>Consectetur, adipisci velit, sed quia non numquam eius modi tempora incidunt ut labore etlarn dolore magnam aliquam quaerat voluptatem. ”</p>
    <div class="name">Client Name</div><div class="city">City</div>
  </blockquote>
  <div class="abs vsep" style="left:268px"></div>
  <blockquote class="abs quote" style="left:289px">
    <p>“ Neque porro quisquam est, qui dolorem ipsum quia dolor sit amet.</p>
    <p>Consectetur, adipisci velit, sed quia non numquam eius modi tempora incidunt ut labore etlarn dolore magnam aliquam quaerat voluptatem. ”</p>
    <div class="name">Client Name</div><div class="city">City</div>
  </blockquote>
  <div class="abs vsep" style="left:498px"></div>
  <blockquote class="abs quote" style="left:522px">
    <p>“ Neque porro quisquam est, qui dolorem ipsum quia dolor sit amet.</p>
    <p>Consectetur, adipisci velit, sed quia non numquam eius modi tempora incidunt ut labore etlarn dolore magnam aliquam quaerat voluptatem. ”</p>
    <div class="name">Client Name</div><div class="city">City</div>
  </blockquote>
</section>

<footer class="abs footer">
  <div class="links">Home &nbsp;-&nbsp; About &nbsp;-&nbsp; Products &nbsp;-&nbsp; Blog &nbsp;-&nbsp; Contact &nbsp;-&nbsp; Register &nbsp;-&nbsp; Login</div>
  <div class="copy">Copyright &nbsp;©&nbsp; 2013 &nbsp;www.velmora.com &nbsp;&nbsp;All rights reserved.</div>
  <a class="social" style="left:626px" aria-label="Social network link"></a>
  <a class="social" style="left:656px" aria-label="Social network link"></a>
  <a class="social" style="left:685px" aria-label="Professional network link"></a>
</footer>

</body>
</html>
```